Harrow Tavern & Grille Menu Makeover

I am looking for a professional look to update our current menu. We are an independently owned sports bar and grill. Up to this point, I have done all of my own graphic designing. I am looking for something classy/family oriented. We are a very family friendly sports bar that offers a wide variety of menu options. Our website is www.harrowtavernco.example. This may help you get more of a feel for what type of place we are and what we offer. Our menu is listed on the website. My current menu is 8.5x14 inserts that feature a cover page, 4 inside pages and a back page. I would like something a little more condensed than this. Possibly a large tri-fold menu? I am open to all new ideas. I do have some pictures on my menu now, and would like to continue using a few pictures to feature some of my items. I would like something that is in a format that gives me the option to change items and prices on my own in the future. I would also like it to feature, or inform my patrons about our technology that we offer. We offer online ordering and we are a "verified venue" with Brewvoke.( a social site for craft beer lovers).

Industry/Entity Type

Sports Bar

Requirements
Nice to have
• Nice to have some pictures, but does not have to. We do feature 9 different beers on tap. A lot of them are local craft beers from the state of Kansas. Not sure if that is something we can feature, but it is a nice talking point. All of our tables and bar are hand built. With a rich mahogany finish on all of our woodwork, some type of "woodgrain" look into the menu would be nice.

```html
<!DOCTYPE html>
<html lang="en">
<head>
<meta charset="utf-8">
<title>Harrow Tavern &amp; Grille — Menu</title>
<link href="https://fonts.googleapis.com/css2?family=Cinzel:wght@400;700&family=Oswald:wght@300;400&family=Montserrat:wght@700&display=swap" rel="stylesheet">
<style>
:root{
  --paper:#ebe7e1;
  --brand-red:#c4323a;
  --panel-red:#c9323c;
  --panel-red-dark:#b7272f;
  --cream:#f3ece4;
  --ink:#1d1b1a;
  --dash:#c94a4f;
  --photo-warm:#b99a52;
  --photo-green:#5d7d3d;
  --photo-dark:#3a3428;
}
*{margin:0;padding:0;box-sizing:border-box}
html,body{width:850px;height:1200px;overflow:hidden;background:var(--paper)}
.menu{position:relative;width:850px;height:1200px;background:var(--paper)}

.brand{position:absolute;top:48px;left:280px;width:290px;text-align:right;
  font-family:"Cinzel",serif;font-weight:700;color:var(--brand-red)}
.brand-name{display:block;font-size:58px;line-height:62px;text-align:center}
.brand-sub{display:block;font-size:22px;line-height:28px;letter-spacing:1px}

.feature-photo{position:absolute;left:90px;top:170px;width:670px;height:220px;
  border:1px dashed var(--dash);
  background:linear-gradient(135deg,var(--photo-dark) 0%,var(--photo-warm) 40%,var(--photo-green) 75%,var(--photo-dark) 100%)}
.photo-tab{position:absolute;left:368px;top:334px;width:112px;height:58px}

.appetizers{position:absolute;left:90px;top:390px;width:670px;height:426px;
  border:1px dashed var(--dash);
  background:radial-gradient(circle at 18% 12%,var(--panel-red-dark),transparent 40%),
    radial-gradient(circle at 80% 70%,#d2464f,transparent 45%),var(--panel-red)}
.section-title{font-family:"Cinzel",serif;text-align:center;line-height:1}
.appetizers .section-title{color:var(--cream);font-weight:400;font-size:40px;margin-top:22px}

.col{position:absolute}
.appetizers .col-left{left:8px;top:66px;width:320px}
.appetizers .col-right{left:337px;top:66px;width:326px}

.item-name{font-family:"Oswald",sans-serif;font-weight:300;font-size:16px;line-height:16px;text-transform:uppercase;letter-spacing:-.3px}
.item-desc{font-family:"Montserrat",sans-serif;font-weight:700;font-size:7.3px;line-height:8px;text-transform:uppercase}
.item-price{font-family:"Montserrat",sans-serif;font-weight:700;font-size:6px;line-height:8px}
.appetizers .item{color:var(--cream);height:48px}
.appetizers .item.h56{height:56px}
.appetizers .item.h64{height:64px}

.salads{position:absolute;left:90px;top:822px;width:670px;height:334px;border:1px dashed var(--dash);
  background:linear-gradient(rgba(240,236,230,.78),rgba(240,236,230,.78)),
    linear-gradient(120deg,#7c9a4e,#c9b057 30%,#b94a3a 55%,#6f8f48 75%,#d7b86a)}
.salads .section-title{color:var(--brand-red);font-weight:700;font-size:35px;margin-top:16px}
.salads .col-left{left:8px;top:64px;width:318px}
.salads .col-right{left:337px;top:64px;width:326px}
.salads .item{color:var(--ink)}
.salads .item-desc{font-family:"Oswald",sans-serif;font-weight:300;font-size:9px;line-height:12px;letter-spacing:-.2px}
.salads .item-price{font-size:5.8px}
.salads .h56{height:56px}
.salads .h64{height:64px}
.salads .h68{height:68px}
</style>
</head>
<body>
<div class="menu">
  <div class="brand">
    <span class="brand-name">Harrow</span>
    <span class="brand-sub">Tavern &amp; Grille</span>
  </div>

  <div class="feature-photo" role="img" aria-label="Photo of featured appetizer: southwest chicken eggrolls with dipping sauce"></div>
  <svg class="photo-tab" viewBox="0 0 112 58" aria-hidden="true">
    <path d="M0 58 C12 58 14 44 19 36 A40 40 0 0 1 93 36 C98 44 100 58 112 58 Z" fill="#c9323c" stroke="#e9e1d6" stroke-width="3"/>
  </svg>

  <section class="appetizers">
    <h2 class="section-title">Appetizers</h2>
    <div class="col col-left">
      <div class="item"><div class="item-name">Slider Burgers</div><div class="item-desc">Six juicy bite sized burgers topped with American cheese and served with pickle slices.</div><div class="item-price">$8.99</div></div>
      <div class="item h56"><div class="item-name">Loaded Potato Skins</div><div class="item-desc">Six crispy skins loaded with jack, cheddar and mozzarella cheese, then topped with smoked bacon and green onions. Served with sour cream.</div><div class="item-price">$8.99</div></div>
      <div class="item"><div class="item-name">Rattlesnake Eggs</div><div class="item-desc">A spicy combo of pepper jack cheese and jalapeños, battered and fried.</div><div class="item-price">$7.99</div></div>
      <div class="item"><div class="item-name">Mozzarella Cheese Sticks</div><div class="item-desc">Classic battered mozzarella cheese sticks served with ranch dressing.</div><div class="item-price">$7.99</div></div>
      <div class="item"><div class="item-name">Grand Slam French Fries</div><div class="item-desc">French fries loaded with jack, cheddar, mozzarella, bacon, jalapeños and green onions! Served with ranch dressing.</div><div class="item-price">$7.99</div></div>
      <div class="item h56"><div class="item-name">Bang Bang Shrimp</div><div class="item-desc">Lightly breaded and fried shrimp coated with a spicy Thai sauce, topped with parmesan cheese and diced tomatoes. Served over a bed of romaine lettuce.</div><div class="item-price">$7.99</div></div>
      <div class="item"><div class="item-name">Ballpark Pretzel Basket</div><div class="item-desc">Buttered and salted pretzels served with nacho cheese sauce.</div><div class="item-price">$7.99</div></div>
    </div>
    <div class="col col-right">
      <div class="item"><div class="item-name">Spicy Southwest Chicken Eggrolls</div><div class="item-desc">Stuffed with black beans, corn and chicken. Served with southwest ranch.</div><div class="item-price">$9.99</div></div>
      <div class="item"><div class="item-name">Blooming Onion</div><div class="item-desc">This fan favorite is classically carved and deep fried to perfection. Served with Harrow signature dipping sauce.</div><div class="item-price">$7.99</div></div>
      <div class="item"><div class="item-name">Chicken Quesadilla</div><div class="item-desc">A 12 inch flour tortilla stuffed with grilled chicken and jack and cheddar cheese. Served with salsa.</div><div class="item-price">$8.99</div></div>
      <div class="item"><div class="item-name">Fenwick's Boneless Buffalo Wings</div><div class="item-desc">A full pound of spicy, boneless buffalo wings. Served with ranch dressing or Fenwick's gold label sauce.</div><div class="item-price">$7.99</div></div>
      <div class="item h64"><div class="item-name">Harrow Loaded Nachos</div><div class="item-desc">Tri-colored tortilla chips smothered with creamy Monterey jack cheese, choice of beef or chicken, and topped with grilled peppers and onions, jalapeños and diced tomatoes. Served with sour cream and salsa.</div><div class="item-price">$9.99</div></div>
      <div class="item h64"><div class="item-name">Garlic Bread Basket</div><div class="item-desc">Tri-colored tortilla chips smothered with creamy Monterey jack cheese, choice of beef or chicken, and topped with grilled peppers and onions, jalapeños and diced tomatoes. Served with sour cream and salsa.</div><div class="item-price">$9.99</div></div>
    </div>
  </section>

  <section class="salads" role="img" aria-label="Faded photo of a fresh garden salad behind the salad listings">
    <h2 class="section-title">Salads</h2>
    <div class="col col-left">
      <div class="item h56"><div class="item-name">Chicken Tender Garden Salad</div><div class="item-desc">A spring lettuce mix topped with shredded jack and cheddar cheese, garden vegetables, bacon, croutons and egg. With your choice of crispy or grilled chicken.</div><div class="item-price">LARGE $8.99 / SMALL $7.99</div></div>
      <div class="item h68"><div class="item-name">Nacho Crunchito Salad</div><div class="item-desc">Harrow' unique blend of iceberg lettuce, topped with jack and cheddar cheese, tomatoes, black olives, ranch style beans and creamy Italian dressing. Topped with crunchito chips</div><div class="item-price">LARGE $8.99 / SMALL $7.99</div></div>
      <div class="item h68"><div class="item-name">Cobb Salad</div><div class="item-desc">Rows of ham, turkey and roast beef, side by side with baby corn, jack and cheddar cheese, egg slices, garden vegetables, bacon and croutons served over iceberg lettuce.</div><div class="item-price">LARGE $8.99 / SMALL $7.99</div></div>
      <div class="item"><div class="item-name">Summer Berry Salad</div><div class="item-desc">A blend of fresh berries, tomatoes, croutons, mandarin oranges and crumbled feta cheese served on fresh spinach leaves. Your choice of chicken or shrimp.</div><div class="item-price">LARGE $8.99 / SMALL $7.99</div></div>
    </div>
    <div class="col col-right">
      <div class="item h64"><div class="item-name">House Caesar Salad</div><div class="item-desc">A classic mix of crisp romaine lettuce, shredded parmesan cheese, and croutons. Served with our signature caesar dressing.</div><div class="item-price">LARGE $6.99 / SMALL $5.99<br>LARGE WITH CHICKEN $8.99 / SMALL WITH CHICKEN $6.99</div></div>
      <div class="item h68"><div class="item-name">Nacho Crunchito Salad</div><div class="item-desc">Harrow' unique blend of iceberg lettuce, topped with jack and cheddar cheese, tomatoes, black olives, ranch style beans and creamy Italian dressing. Topped with crunchito chips</div><div class="item-price">LARGE $8.99 / SMALL $7.99</div></div>
      <div class="item h68"><div class="item-name">Cobb Salad</div><div class="item-desc">Rows of ham, turkey and roast beef, side by side with baby corn, jack and cheddar cheese, egg slices, garden vegetables, bacon and croutons served over iceberg lettuce.</div><div class="item-price">LARGE $8.99 / SMALL $7.99</div></div>
      <div class="item"><div class="item-name">Summer Berry Salad</div><div class="item-desc">A blend of fresh berries, tomatoes, croutons, mandarin oranges and crumbled feta cheese served on fresh spinach leaves. Your choice of chicken or shrimp.</div><div class="item-price">LARGE $8.99 / SMALL $7.99</div></div>
    </div>
  </section>
</div>
</body>
</html>
```